Business cards to launch an education platform

Hi,
I am looking at having new business cards designed.
I am a startup, developing a web platform for schools and university, the education world. It's an online assessment system.
I would like a card that looks classy, and that is using the colors and the font of my logo.

I have attached:
1) my logo
2) A business card that I have designed quickly so you can have all the information required in the card, but I really don't like it.
3) The font that I am using (Lato Regular) to design my web platform
4) Some screenshots of my web platform so you can have a look at the style that I have.

Target Market(s)

Major market: Education system: Schools and university
Minor markets: Business in general

Industry/Entity Type

Business

Contact Information for Business Card

Clara Fenwick
Director

M: 0437 518 902
E: clara.fenwick@amberLoomSystems.com.au

Requirements
Must have
• The colors of my logo

```html
<!DOCTYPE html>
<html lang="en">
<head>
<meta charset="utf-8">
<title>Amber Loom Systems – Business Cards</title>
<link href="https://fonts.googleapis.com/css2?family=Lato:wght@400;700&display=swap" rel="stylesheet">
<style>
  :root {
    --backdrop: #eceff2;
    --brand-blue: #0571bc;
    --brand-sky: #23b3e6;
    --brand-navy: #1c4e80;
    --white: #ffffff;
  }
  * { margin: 0; padding: 0; box-sizing: border-box; }
  html, body {
    width: 1200px; height: 900px; overflow: hidden;
    background: var(--backdrop);
    font-family: "Lato", sans-serif;
  }
  .canvas { position: relative; width: 1200px; height: 900px; }
  .card {
    position: absolute;
    width: 556px; height: 345px;
    box-shadow: 0 6px 18px rgba(0,0,0,0.15);
    overflow: hidden;
  }
  /* Front */
  .card-front { left: 238px; top: 60px; background: var(--brand-blue); color: var(--white); }
  .front-side-panel {
    position: absolute; left: 418px; top: 0; width: 138px; height: 100%;
    background: var(--brand-sky);
    border-left: 8px solid var(--white);
  }
  .front-square {
    position: absolute; left: 352px; top: 116px; width: 114px; height: 114px;
    background: var(--white);
  }
  .brand-name-front { position: absolute; left: 34px; top: 38px; }
  .brand-name-front .brand-main {
    font-size: 40px; letter-spacing: 4px; font-weight: 400; line-height: 1;
  }
  .brand-name-front .brand-sub {
    font-size: 27px; letter-spacing: 3px; font-weight: 700; line-height: 1.1; margin-top: 4px;
  }
  .contact-person { position: absolute; left: 27px; top: 200px; }
  .person-name { font-size: 22px; font-weight: 400; line-height: 1.1; }
  .person-role { font-size: 14px; margin-top: 4px; }
  .contact-list { list-style: none; margin-top: 20px; font-size: 15px; }
  .contact-list li { display: flex; align-items: center; gap: 8px; line-height: 21px; }
  .contact-list svg { width: 12px; height: 12px; fill: var(--white); flex: none; }
  /* Back */
  .card-back { left: 457px; top: 518px; width: 560px; height: 344px; background: var(--white); }
  .back-lockup {
    position: absolute; left: 112px; top: 112px;
    display: flex; align-items: center; gap: 16px;
  }
  .back-square { width: 104px; height: 104px; background: var(--brand-blue); }
  .back-name .brand-main {
    font-size: 36px; letter-spacing: 3px; color: var(--brand-navy); line-height: 1;
  }
  .back-name .brand-sub {
    font-size: 24px; letter-spacing: 2.5px; font-weight: 700; color: var(--brand-sky); line-height: 1.2;
  }
</style>
</head>
<body>
<main class="canvas">
  <section class="card card-front">
    <div class="front-side-panel"></div>
    <div class="front-square"></div>
    <div class="brand-name-front">
      <div class="brand-main">AMBER</div>
      <div class="brand-sub">Loom systems</div>
    </div>
    <div class="contact-person">
      <div class="person-name">Clara Fenwick</div>
      <div class="person-role">Director</div>
      <ul class="contact-list">
        <li>
          <svg viewBox="0 0 24 24" aria-hidden="true"><path d="M6.6 10.8a15.1 15.1 0 0 0 6.6 6.6l2.2-2.2a1 1 0 0 1 1-.25 11.4 11.4 0 0 0 3.6.57 1 1 0 0 1 1 1V20a1 1 0 0 1-1 1A17 17 0 0 1 3 4a1 1 0 0 1 1-1h3.5a1 1 0 0 1 1 1c0 1.25.2 2.45.57 3.6a1 1 0 0 1-.25 1z"/></svg>
          0437 518 902
        </li>
        <li>
          <svg viewBox="0 0 24 24" aria-hidden="true"><path d="M2 5h20v14H2z M2 5l10 8 10-8" /></svg>
          clara.fenwick@amberLoomSystems.com.au
        </li>
      </ul>
    </div>
  </section>

  <section class="card card-back">
    <div class="back-lockup">
      <div class="back-square"></div>
      <div class="back-name">
        <div class="brand-main">AMBER</div>
        <div class="brand-sub">Loom systems</div>
      </div>
    </div>
  </section>
</main>
</body>
</html>
```